Construction Company

Design a clutter free business card, it can be double-sided utilizing the logo for VKM Ltd simple with all relevant contact information.

Please also a letterhead design to function for the purposes of invoicing, all mail requirements, with header to be distinctive while the footer ties page together and incorporates all necessary information.

For now, please use generic / dummy text and when a winner is selected, I will disclose the contact information.

Hi Designers! Please read the updated brief which includes the design of a business card and letterhead. Thank you!

```html
<!DOCTYPE html>
<html lang="en">
<head>
<meta charset="UTF-8">
<title>VKM Ltd Business Card</title>
<link href="https://fonts.googleapis.com/css2?family=Open+Sans:wght@400;600;700&display=swap" rel="stylesheet">
<style>
  :root {
    --brand-blue: #283d8f;
    --brand-gold: #b0902f;
    --paper: #ffffff;
    --ink-grey: #4a4a4a;
    --backdrop: #e6e4e0;
  }
  * { margin: 0; padding: 0; box-sizing: border-box; }
  html, body { width: 1200px; height: 900px; overflow: hidden; }
  body {
    background: var(--backdrop);
    font-family: "Open Sans", Arial, sans-serif;
    position: relative;
  }
  .card {
    position: absolute;
    left: 240px;
    width: 720px;
    height: 411px;
    box-shadow: 0 6px 18px rgba(0,0,0,0.18);
    overflow: hidden;
  }
  .card-front { top: 24px; background: var(--brand-blue); }
  .card-back { top: 465px; background: var(--paper); }

  .wordmark {
    position: absolute;
    display: flex;
    align-items: center;
    gap: 14px;
    font-weight: 700;
    letter-spacing: 2px;
    white-space: nowrap;
  }
  .wordmark-dot { border-radius: 50%; flex: none; }
  .card-front .wordmark {
    left: 50%; top: 50%;
    transform: translate(-50%, -50%);
    font-size: 64px;
    color: var(--paper);
  }
  .card-front .wordmark-dot { width: 26px; height: 26px; background: var(--paper); }
  .card-back .wordmark {
    right: 60px; top: 68px;
    font-size: 46px;
    color: var(--brand-blue);
  }
  .card-back .wordmark-dot { width: 18px; height: 18px; background: var(--brand-blue); }

  .rule-long {
    position: absolute;
    left: 300px; right: 56px; top: 178px;
    height: 1.5px; background: var(--brand-blue);
  }
  .holder { position: absolute; left: 60px; top: 186px; }
  .holder-name {
    font-weight: 700; font-size: 27px; color: var(--brand-blue);
    letter-spacing: 0.3px; line-height: 1.1;
  }
  .holder-title { font-size: 19px; color: var(--ink-grey); margin-top: 2px; }
  .rule-short {
    position: absolute;
    left: 60px; width: 230px; top: 270px;
    height: 1.5px; background: var(--brand-blue);
  }
  .contact-list {
    position: absolute; left: 60px; top: 282px;
    list-style: none;
  }
  .contact-list li {
    display: flex; align-items: center; gap: 10px;
    font-size: 18px; color: var(--ink-grey); line-height: 27px;
  }
  .contact-list svg { width: 15px; height: 15px; flex: none; }
  .address {
    position: absolute; right: 60px; top: 190px;
    text-align: right; font-size: 18px; color: var(--ink-grey); line-height: 25px;
  }
  .footer-bands { position: absolute; left: 0; bottom: 0; width: 720px; height: 90px; }
  .website {
    position: absolute; right: 40px; bottom: 24px;
    font-size: 17px; color: var(--paper); letter-spacing: 0.3px;
  }
</style>
</head>
<body>
  <section class="card card-front" aria-label="Card front">
    <div class="wordmark"><span class="wordmark-dot"></span>VKM Ltd</div>
  </section>

  <section class="card card-back" aria-label="Card back">
    <div class="wordmark"><span class="wordmark-dot"></span>VKM Ltd</div>
    <div class="rule-long"></div>

    <div class="holder">
      <p class="holder-name">DANIEL HARROW</p>
      <p class="holder-title">President</p>
    </div>
    <div class="rule-short"></div>

    <ul class="contact-list">
      <li>
        <svg viewBox="0 0 16 16"><path fill="#b0902f" d="M3.5 1.5l2.5 3-1.4 1.6c.9 2 2.4 3.5 4.4 4.4l1.6-1.4 3 2.5-1.6 2.4C7 14 2 9 1.1 3.1z"/></svg>
        555-310-4827
      </li>
      <li>
        <svg viewBox="0 0 16 16"><rect x="4" y="1" width="8" height="14" rx="1.5" fill="none" stroke="#b0902f" stroke-width="1.6"/><circle cx="8" cy="12.3" r="0.9" fill="#b0902f"/></svg>
        555-310-4827
      </li>
      <li>
        <svg viewBox="0 0 16 16"><rect x="1" y="3.5" width="14" height="9" fill="#b0902f"/><path d="M1 3.5l7 5 7-5" fill="none" stroke="#fff" stroke-width="1.2"/></svg>
        dharrow@vkmltd.com
      </li>
    </ul>

    <p class="address">3175 Bayfront Drive<br>Cove City CA 90412</p>

    <svg class="footer-bands" viewBox="0 0 720 90" preserveAspectRatio="none" aria-hidden="true">
      <polygon points="0,63 505,63 513,55 720,55 720,59 516,59 508,67 0,67" fill="#b0902f"/>
      <polygon points="0,78 515,78 525,40 720,40 720,90 0,90" fill="#283d8f"/>
    </svg>
    <p class="website">www.vkmltd.com</p>
  </section>
</body>
</html>
```